redesign my website bluekeelvoyages.net and make it user friendly

I already have a website, bluekeelvoyages.net, and want a redesign in WordPress with Elementor Pro, using the same text/content. The goal is to improve:

Design quality (colors, fonts, spacing, visual flow)
User experience (easy navigation, clear offers)
Conversion readiness (calls-to-action, trust signals, booking flow)
Technical side (SEO basics, fast speed, full mobile responsiveness)

The site should look modern, clean, fun, engaging, interactive and optimized for speed and usability.

I would like the 11 page to be consolidate dto 6 as follows: Home (main landing, highlights)

Sailboat Trips (all packages, itineraries, pricing)
Boats (fleet details, features, photos)
How It Works (booking process, FAQs, travel info, what to expect)
Blog
Contact Us (form, Messaging, phone, etc.)

Target Market(s)

sailboat trip customers for San Blas Islands in Panama

Industry/Entity Type

Travel, Boat Tour Agency

Coding

Coded - Design and coding required

Number of Pages Required

3 page

Font styles to use
Sans Serif
Other font styles liked:
• Oswalg and sans serif

Colors
0054AA
0677BA
7BADD7
CADEEF
E8F1F8
0094D4
00A9DD
6FCCEA
C7EBF8
E9F6FB
FFC000
F8CF3A
FAE287
FDF2CF
FEFAEE
F0912C
F2A743
F7CA91
FBE8D2
FDF5EE

Requirements
Must have
• Home (main landing, highlights) Sailboat Trips (all packages, itineraries, pricing) Boats (fleet details, features, photos) How It Works (booking process, FAQs, travel info, what to expect) Blog (updates, travel tips, inspiration) Contact Us (form, Messaging, phone, etc.)
Nice to have
• I want it to look professionla and be very user friendy to entice people to contact me to book boat trips
Should not have
• a store

```html
<!DOCTYPE html>
<html lang="en">
<head>
<meta charset="utf-8">
<title>Blue Keel Voyages – San Blas Sailing</title>
<link href="https://fonts.googleapis.com/css2?family=Oswald:wght@500;600&family=Poppins:wght@400;500;600&display=swap" rel="stylesheet">
<style>
:root{
  --blue:#1f4aa8;
  --blue-dark:#163a8c;
  --orange:#e08433;
  --ink:#1b1b1b;
  --text:#333;
  --white:#fff;
}
*{box-sizing:border-box;margin:0;padding:0}
html,body{width:1200px;height:4292px;overflow:hidden}
body{font-family:'Poppins',sans-serif;color:var(--text);background:var(--white);position:relative}
.abs{position:absolute}
.heading{font-family:'Oswald',sans-serif;font-weight:500;color:var(--ink);text-align:center}
.rule{position:absolute;width:70px;height:3px;border-radius:2px;background:var(--blue)}
.rule.light{background:var(--white)}
.btn{position:absolute;background:var(--orange);color:var(--white);font-family:'Poppins',sans-serif;font-weight:600;font-size:14px;border-radius:24px;display:flex;align-items:center;justify-content:center;letter-spacing:.3px;text-transform:uppercase}

/* header */
.topbar{position:absolute;left:625px;top:0;width:575px;height:47px;background:var(--blue);clip-path:polygon(30px 0,100% 0,100% 100%,0 100%)}
.topbar ul{list-style:none;display:flex;position:absolute;left:48px;top:15px;font-size:12px;color:var(--white)}
.topbar li{margin-right:44px}
.brand{position:absolute;left:140px;top:52px;display:flex;align-items:center;gap:12px}
.brand-dot{width:34px;height:34px;border-radius:50%;background:var(--blue)}
.brand-name{font-family:'Oswald',sans-serif;font-weight:600;font-size:24px;color:var(--ink);letter-spacing:.3px}
.mainnav{position:absolute;top:86px;left:475px;font-size:12px;color:var(--ink)}
.mainnav span{position:absolute;white-space:nowrap}
.mainnav .active{font-weight:600;border-bottom:1px solid var(--ink);padding-bottom:2px}

/* hero */
.hero{position:absolute;left:0;top:137px;width:1200px;height:520px;overflow:hidden}
.hero-photo{position:absolute;inset:0;background:linear-gradient(180deg,#3f7fcc 0%,#8fb7e4 35%,#bfd6ee 55%,#3d78c4 62%,#1c5fb0 100%)}
.hero-title{position:absolute;left:120px;top:95px;font-family:'Oswald',sans-serif;font-weight:600;color:var(--white);font-size:70px;line-height:1.1}
.hero-sub{position:absolute;left:120px;top:180px;font-family:'Oswald',sans-serif;font-weight:500;color:var(--white);font-size:40px;line-height:49px}

/* about */
.about-title{position:absolute;left:0;width:1200px;top:722px;font-size:40px}
.about-text{position:absolute;left:190px;width:818px;top:815px;font-size:13.5px;line-height:24px;text-align:center}
.tours-title{position:absolute;left:0;width:1200px;top:1025px;font-size:40px}

.tour-card{position:absolute;top:1128px;width:285px;height:342px;background:var(--white);box-shadow:0 2px 10px rgba(0,0,0,.12);text-align:center}
.tour-card.featured{background:var(--blue);color:var(--white)}
.tour-icon{position:absolute;left:88px;top:18px;width:110px;height:110px}
.tour-card h3{position:absolute;top:155px;width:100%;font-size:17px;font-weight:500;color:var(--ink)}
.tour-card.featured h3{color:var(--white)}
.tour-card p{position:absolute;top:190px;left:14px;right:14px;font-size:12.5px;line-height:25px;color:#555}
.tour-card.featured p{color:var(--white)}
.tour-arrow{position:absolute;left:122px;top:282px}

/* fleet band */
.fleet-band{position:absolute;left:0;top:1620px;width:1200px;height:735px;background:var(--blue)}
.fleet-title{position:absolute;left:0;width:1200px;top:1705px;font-size:40px;color:var(--white)}
.boat{position:absolute;top:1820px;width:288px;height:375px;overflow:hidden}
.boat-photo{position:absolute;inset:0}
.boat-tag{position:absolute;left:14px;top:252px;background:var(--orange);color:var(--white);font-family:'Oswald',sans-serif;font-size:15px;padding:1px 10px}
.boat-name{position:absolute;left:14px;top:280px;font-family:'Oswald',sans-serif;font-weight:500;font-size:28px;color:var(--white)}
.boat-specs{position:absolute;left:0;bottom:0;width:100%;height:52px;background:rgba(10,20,40,.92);display:flex;align-items:center;justify-content:space-around;padding:0 10px;color:var(--white);font-family:'Oswald',sans-serif;font-size:16px}
.slider-arrow{position:absolute;top:1943px}

/* testimonials */
.reviews-title{position:absolute;left:0;width:1200px;top:2408px;font-size:40px}
.review-card{position:absolute;left:152px;top:2532px;width:890px;height:380px;background:var(--white);box-shadow:0 3px 14px rgba(0,0,0,.15);border-radius:6px}
.review-photo{position:absolute;left:8px;top:5px;width:420px;height:370px;border-radius:4px;background:linear-gradient(180deg,#bcd2ea 0%,#7aa3cf 40%,#2f6fae 70%,#1f5792 100%)}
.review-text{position:absolute;left:465px;top:78px;width:402px;font-size:13.3px;line-height:24px;text-align:justify}
.ghost{position:absolute;top:2535px;height:375px;background:var(--white);box-shadow:0 3px 12px rgba(0,0,0,.08);opacity:.6}
.dots{position:absolute;left:565px;top:2951px;display:flex;gap:10px}
.dots i{width:14px;height:14px;border-radius:50%;border:2px solid var(--ink);display:block}
.dots i.on{background:var(--ink)}

/* booking */
.book-bg{position:absolute;left:0;top:3000px;width:1200px;height:952px;background:linear-gradient(180deg,#fff 0%,#fff 55%,#e6eef7 68%,#a9c6e6 80%,#4f87c4 90%,#2d68ad 100%)}
.book-title{position:absolute;left:120px;top:3085px;font-family:'Oswald',sans-serif;font-weight:500;font-size:40px;color:var(--ink)}
.book-text{position:absolute;left:120px;top:3200px;width:375px;font-size:13.3px;line-height:24px;text-align:justify}
.contact-row{position:absolute;left:120px;display:flex;align-items:flex-start;gap:25px}
.contact-icon{width:60px;height:60px;border-radius:50%;background:var(--blue);display:flex;align-items:center;justify-content:center}
.contact-row h4{font-size:21px;font-weight:500;color:var(--ink)}
.contact-row p{font-size:15px;color:#555;margin-top:4px}
.social{position:absolute;top:3543px;left:127px;display:flex;gap:18px;font-size:13px;font-weight:500;color:var(--ink)}
.social span{display:flex;align-items:center;gap:7px}
.social i{width:24px;height:24px;border-radius:50%;background:var(--blue);display:block}

.form-shadow{position:absolute;left:610px;top:3705px;width:443px;height:150px;background:var(--blue);border-radius:0 0 10px 10px}
.form-card{position:absolute;left:620px;top:3035px;width:423px;height:800px;background:var(--orange);border-radius:14px}
.form-card h3{position:absolute;left:38px;top:22px;font-size:17px;font-weight:400;color:var(--white)}
.flabel{position:absolute;font-size:12px;font-weight:600;color:var(--white)}
.field{position:absolute;background:var(--white);border:1px solid #d0d0d0;font-size:12px;color:#444;display:flex;align-items:center;padding-left:10px}
.field svg{position:absolute;right:10px}
.submit{position:absolute;left:660px;top:3760px;width:158px;height:42px;border-radius:22px;background:var(--blue);color:var(--white);font-weight:600;font-size:14px;display:flex;align-items:center;justify-content:center}

/* footer */
.footer{position:absolute;left:0;top:3950px;width:1200px;height:342px;background:var(--blue)}
.footer-brand{position:absolute;left:0;width:1200px;top:98px;display:flex;justify-content:center;align-items:center;gap:14px}
.footer-brand .brand-dot{background:var(--white)}
.footer-brand .brand-name{color:var(--white)}
.footer-links{position:absolute;left:0;width:1200px;top:218px;display:flex;justify-content:center;gap:24px;font-size:15px;color:var(--white)}
.footer-rule{position:absolute;left:120px;top:280px;width:960px;height:1px;background:rgba(255,255,255,.55)}
.copyright{position:absolute;left:0;width:1200px;top:302px;text-align:center;font-size:12px;color:var(--white)}
</style>
</head>
<body>

<header>
  <div class="topbar">
    <ul><li>PRICING</li><li>TINERARIES</li><li>ACTIVITIES</li><li>BLOG</li><li>FAQS</li></ul>
  </div>
  <div class="brand">
    <span class="brand-dot"></span>
    <span class="brand-name">BLUE KEEL VOYAGES</span>
  </div>
  <nav class="mainnav">
    <span class="active" style="left:0">HOME</span>
    <span style="left:75px">GUNA YALA</span>
    <span style="left:180px">FLEET</span>
    <span style="left:247px">ABOUT US</span>
    <span style="left:342px">BOOK NOW</span>
  </nav>
  <div class="btn" style="left:920px;top:72px;width:160px;height:43px">Contact Us</div>
</header>

<section class="hero">
  <div class="hero-photo" role="img" aria-label="White sailboat on calm blue sea under a cloudy sky"></div>
  <h1 class="hero-title">San Blas Islands</h1>
  <p class="hero-sub">Panama Sailing Vacations<br>Ultimate Beaches &amp;<br>Catamaran Tours</p>
  <div class="btn" style="left:122px;top:353px;width:158px;height:40px;font-size:13px">Inquire Now</div>
</section>

<h2 class="heading about-title">About Us</h2>
<span class="rule" style="left:565px;top:782px"></span>
<p class="about-text">We're sailors and travelers with a love for exploration. When we first arrived in San Blas, its unique beauty and culture left a lasting impression. What began as a stop along our journey soon became something more—we felt a strong connection to this place and a sincere respect for its people, traditions, and way of life. Rather than simply making it our home, we've done our best to live in harmony with the environment and the values of the local community. Today, our mission is to share the experience of San Blas with others through safe, sustainable, and memorable sailing adventures. We do this by building trusted partnerships, ensuring the visitors we bring maintain a respectful presence, and guiding every trip with care, cultural sensitivity, and a commitment to quality.</p>

<h2 class="heading tours-title">Discover Ultimate Panama Sailing Tours</h2>
<span class="rule" style="left:565px;top:1094px"></span>

<article class="tour-card" style="left:145px">
  <svg class="tour-icon" viewBox="0 0 110 110"><circle cx="55" cy="55" r="52" fill="none" stroke="#1f4aa8" stroke-width="2" stroke-dasharray="6 4"/><circle cx="55" cy="55" r="43" fill="#1f4aa8"/><path d="M55 30 L55 66 M55 32 L72 64 L55 64 M53 38 L40 64 L53 64" stroke="#fff" stroke-width="2.5" fill="none"/><path d="M36 70 L74 70 L68 78 L42 78Z" fill="#fff"/></svg>
  <h3>Private Charters</h3>
  <p>Sail the beautiful islands and beaches of San Blas on a private all-inclusive catamaran. Enjoy a custom itinerary.</p>
  <svg class="tour-arrow" width="42" height="42" viewBox="0 0 42 42"><circle cx="21" cy="21" r="19" fill="none" stroke="#1b1b1b" stroke-width="2"/><path d="M12 21 H29 M23 15 L29 21 L23 27" stroke="#1b1b1b" stroke-width="2" fill="none"/></svg>
</article>
<article class="tour-card featured" style="left:458px">
  <svg class="tour-icon" viewBox="0 0 110 110"><circle cx="55" cy="55" r="52" fill="none" stroke="#fff" stroke-width="2" stroke-dasharray="6 4"/><circle cx="55" cy="55" r="43" fill="#e08433"/><circle cx="55" cy="47" r="8" fill="none" stroke="#fff" stroke-width="2.5"/><path d="M40 72 Q55 54 70 72" stroke="#fff" stroke-width="2.5" fill="none"/><circle cx="34" cy="55" r="5" fill="none" stroke="#fff" stroke-width="2"/><circle cx="76" cy="55" r="5" fill="none" stroke="#fff" stroke-width="2"/></svg>
  <h3>Shared Charters</h3>
  <p>Share the experience with others for a more affordable alternative to a private charter. Perfect for couples,</p>
  <svg class="tour-arrow" width="42" height="42" viewBox="0 0 42 42"><circle cx="21" cy="21" r="19" fill="none" stroke="#fff" stroke-width="2"/><path d="M12 21 H29 M23 15 L29 21 L23 27" stroke="#fff" stroke-width="2" fill="none"/></svg>
</article>
<article class="tour-card" style="left:770px">
  <svg class="tour-icon" viewBox="0 0 110 110"><circle cx="55" cy="55" r="52" fill="none" stroke="#1f4aa8" stroke-width="2" stroke-dasharray="6 4"/><circle cx="55" cy="55" r="43" fill="#1f4aa8"/><path d="M36 30 a7 7 0 1 1 14 0 c0 6 -7 12 -7 12 c0 0 -7 -6 -7 -12Z" fill="none" stroke="#fff" stroke-width="2"/><path d="M62 70 a7 7 0 1 1 14 0 c0 6 -7 12 -7 12 c0 0 -7 -6 -7 -12Z" fill="none" stroke="#fff" stroke-width="2"/><path d="M43 44 Q43 62 62 70" stroke="#fff" stroke-width="2" stroke-dasharray="3 3" fill="none"/></svg>
  <h3>Family Friendly Boat Trips</h3>
  <p>San Blas is perfect for kids, with calm waters, safe snorkeling, and fun island-hopping.</p>
  <svg class="tour-arrow" width="42" height="42" viewBox="0 0 42 42"><circle cx="21" cy="21" r="19" fill="none" stroke="#1b1b1b" stroke-width="2"/><path d="M12 21 H29 M23 15 L29 21 L23 27" stroke="#1b1b1b" stroke-width="2" fill="none"/></svg>
</article>

<div class="btn" style="left:508px;top:1517px;width:180px;height:45px">Request a Quote</div>

<div class="fleet-band"></div>
<h2 class="heading fleet-title">Featured Catamarans</h2>
<span class="rule light" style="left:565px;top:1772px"></span>

<svg class="slider-arrow" style="left:48px" width="32" height="32" viewBox="0 0 32 32"><circle cx="16" cy="16" r="14" fill="none" stroke="#fff" stroke-width="2"/><path d="M22 16 H10 M15 11 L10 16 L15 21" stroke="#fff" stroke-width="2" fill="none"/></svg>
<svg class="slider-arrow" style="left:1118px" width="32" height="32" viewBox="0 0 32 32"><circle cx="16" cy="16" r="14" fill="none" stroke="#fff" stroke-width="2"/><path d="M10 16 H22 M17 11 L22 16 L17 21" stroke="#fff" stroke-width="2" fill="none"/></svg>

<article class="boat" style="left:140px">
  <div class="boat-photo" role="img" aria-label="Guests on the deck of a catamaran" style="background:linear-gradient(180deg,#dfe3e8 0%,#b9c0c8 45%,#6d7782 80%,#2b3340 100%)"></div>
  <span class="boat-tag">Catamaran</span>
  <span class="boat-name">Marea 42</span>
  <div class="boat-specs"><span>42 ft</span><span>3 cabin</span><span>8 Guest</span></div>
</article>
<article class="boat" style="left:460px">
  <div class="boat-photo" role="img" aria-label="Catamaran anchored in turquoise water near a palm island" style="background:linear-gradient(180deg,#5d7f4a 0%,#c8b58a 30%,#5fc3c0 55%,#2a8fa6 80%,#1d3f5a 100%)"></div>
  <span class="boat-tag">Catamaran</span>
  <span class="boat-name">Coral 55F</span>
  <div class="boat-specs"><span>55 ft</span><span>4 Cabin</span><span>8 Guest</span></div>
</article>
<article class="boat" style="left:778px">
  <div class="boat-photo" role="img" aria-label="Catamaran with tall mast under blue sky" style="background:linear-gradient(180deg,#3d7fd6 0%,#8db8ea 40%,#c9d4dc 60%,#4b5c6c 85%,#1e2733 100%)"></div>
  <span class="boat-tag">Catamaran</span>
  <span class="boat-name">Coral 37</span>
  <div class="boat-specs"><span>37 ft</span><span>3 cabin</span><span>6 Guest</span></div>
</article>

<div class="btn" style="left:493px;top:2237px;width:212px;height:40px;font-size:13px">See All Boats &amp; Prices</div>

<h2 class="heading reviews-title">What Our Client say</h2>
<span class="rule" style="left:560px;top:2476px"></span>

<div class="ghost" style="left:-10px;width:80px"></div>
<div class="ghost" style="left:1095px;width:120px;background:linear-gradient(180deg,#e2ebf4,#c9d9ea)"></div>

<article class="review-card">
  <div class="review-photo" role="img" aria-label="Happy guests swimming beside a catamaran"></div>
  <svg class="abs" style="left:468px;top:32px" width="38" height="30" viewBox="0 0 38 30"><path d="M2 28 V16 Q2 4 14 2 V8 Q8 10 8 16 H14 V28Z M22 28 V16 Q22 4 34 2 V8 Q28 10 28 16 H34 V28Z" fill="#e08433"/></svg>
  <p class="review-text">Wow. We absolutely loved loved loved our time sailing through the San Blas islands. The food was absolutely amazing (highlights of lobster and octopus!) and enjoyed the daily cocktails after a day of relaxing while sailing through, snorkelling with captain Mateo and paddle boarding in paradise. The company were super helpful in organising the trip and our transport to get there from Panama City with excellent communication via chat. The bedrooms and bathrooms are functional enough - we spent all our time outside anyway. Would not hesitate to recommend and I hope to go back one day!</p>
</article>
<div class="dots"><i class="on"></i><i></i><i></i></div>

<div class="book-bg" role="img" aria-label="Calm sea horizon with a distant sailboat"></div>
<h2 class="book-title">BOOK AN ADVENTURE</h2>
<span class="rule" style="left:120px;top:3158px"></span>
<p class="book-text">Discover unforgettable catamaran and sailboat adventures in Guna Yala (San Blas), Panama. Blue Keel Voyages LLC offers all-inclusive island-hopping, snorkeling, and immersive cultural experiences—trusted by travelers worldwide.</p>

<div class="contact-row" style="top:3353px">
  <div class="contact-icon"><svg width="30" height="22" viewBox="0 0 30 22"><rect x="1" y="1" width="28" height="20" rx="2" fill="none" stroke="#fff" stroke-width="2"/><path d="M2 3 L15 13 L28 3" stroke="#fff" stroke-width="2" fill="none"/></svg></div>
  <div><h4>Email Us</h4><p>hello@bluekeelvoyages.net</p></div>
</div>
<div class="contact-row" style="top:3440px">
  <div class="contact-icon"><svg width="26" height="26" viewBox="0 0 24 24"><path d="M6.6 10.8a15 15 0 006.6 6.6l2.2-2.2a1 1 0 011-.25 11.4 11.4 0 003.6.57 1 1 0 011 1V20a1 1 0 01-1 1A17 17 0 013 4a1 1 0 011-1h3.5a1 1 0 011 1c0 1.25.2 2.45.57 3.57a1 1 0 01-.25 1z" fill="#fff"/></svg></div>
  <div><h4>Call Us</h4><p>+57 300 555 0142</p></div>
</div>
<div class="social">
  <span><i></i>Keelbook</span>
  <span><i></i>Snapdeck</span>
  <span><i></i>Wavetube</span>
</div>

<div class="form-shadow"></div>
<form class="form-card">
  <h3>Book an Adventure</h3>
</form>
<span class="flabel" style="left:670px;top:3100px">Name</span>
<div class="field" style="left:662px;top:3128px;width:350px;height:37px">John Andrew<svg width="16" height="16" viewBox="0 0 16 16"><circle cx="8" cy="5" r="3.5" fill="none" stroke="#333" stroke-width="1.4"/><path d="M2 15 Q8 7 14 15Z" fill="none" stroke="#333" stroke-width="1.4"/></svg></div>
<span class="flabel" style="left:670px;top:3183px">Email Address*</span>
<div class="field" style="left:662px;top:3210px;width:350px;height:38px">john.andrew@example.net<svg width="18" height="14" viewBox="0 0 18 14"><rect x="1" y="1" width="16" height="12" fill="none" stroke="#333" stroke-width="1.4"/><path d="M1 1 L9 8 L17 1" stroke="#333" stroke-width="1.4" fill="none"/></svg></div>
<span class="flabel" style="left:670px;top:3265px">Messaging Number*</span>
<div class="field" style="left:662px;top:3288px;width:350px;height:39px">+1888 888 8888<svg width="18" height="18" viewBox="0 0 18 18"><circle cx="9" cy="9" r="7.5" fill="none" stroke="#333" stroke-width="1.4"/><path d="M6 6.5 Q7 11 11.5 12" stroke="#333" stroke-width="1.4" fill="none"/></svg></div>

<span class="flabel" style="left:670px;top:3350px">Select Charter</span>
<span class="flabel" style="left:851px;top:3350px">Number of Passengers</span>
<div class="field" style="left:662px;top:3378px;width:168px;height:40px">Private Charter<svg width="12" height="8" viewBox="0 0 12 8"><path d="M1 1 L6 6 L11 1" stroke="#333" stroke-width="1.6" fill="none"/></svg></div>
<div class="field" style="left:843px;top:3378px;width:169px;height:40px">1<svg width="12" height="8" viewBox="0 0 12 8"><path d="M1 1 L6 6 L11 1" stroke="#333" stroke-width="1.6" fill="none"/></svg></div>

<span class="flabel" style="left:670px;top:3438px">Number of Days</span>
<span class="flabel" style="left:856px;top:3438px">Date</span>
<div class="field" style="left:662px;top:3468px;width:168px;height:40px">1<svg width="12" height="8" viewBox="0 0 12 8"><path d="M1 1 L6 6 L11 1" stroke="#333" stroke-width="1.6" fill="none"/></svg></div>
<div class="field" style="left:843px;top:3468px;width:169px;height:40px">MM/DD/YYYY<svg width="12" height="8" viewBox="0 0 12 8"><path d="M1 1 L6 6 L11 1" stroke="#333" stroke-width="1.6" fill="none"/></svg></div>

<span class="flabel" style="left:670px;top:3528px;line-height:18px">What type of experience are you looking for?<br>(Check all that apply)</span>
<div class="field" style="left:662px;top:3580px;width:350px;height:38px">Select<svg width="12" height="8" viewBox="0 0 12 8"><path d="M1 1 L6 6 L11 1" stroke="#333" stroke-width="1.6" fill="none"/></svg></div>
<div class="field" style="left:662px;top:3635px;width:350px;height:98px;align-items:flex-start;padding-top:12px">Message</div>
<div class="submit">SUBMIT</div>

<footer class="footer">
  <div class="footer-brand"><span class="brand-dot"></span><span class="brand-name">BLUE KEEL VOYAGES</span></div>
  <nav class="footer-links"><span>Home</span><span>Guna Yala</span><span>Fleet</span><span>About Us</span><span>Book Now</span><span>Pricing</span><span>Itineraries</span><span>Activities</span><span>Blog</span><span>FAQs</span><span>Contact Us</span></nav>
  <div class="footer-rule"></div>
  <p class="copyright">© 2025 Blue Keel Voyages &nbsp;Privacy Policy &nbsp;Terms &amp; Conditions</p>
</footer>

</body>
</html>
```